female esthetician looking for an impact business card

I an an expert in skin care industry with high experience in NYC.I want my business card to look professional , an impact at first look. I do want a combination between white and gold . I believe the font will be great if is gold.. The Fonts are also important. MIRABELA COSTINA (SKIN CARE BOUTIQUE)

THIS SHOULD BE THE BUSINESS NAME, and should be placed on th eback of the card.
IN front m, the name MIRABELA COSTINA - ESTHETCIAN

BY APPOINTMENTS ONLY: 518.240.7136

Target Market(s)

HIGH END CLIENTELE

Contact Information for Business Card

iT WILL BE on a luxury paper. I neeed the wow feeling

Requirements
Should not have
• pictures

```html
<!DOCTYPE html>
<html lang="en">
<head>
<meta charset="utf-8">
<title>Mirabela Costina – Business Card</title>
<link rel="stylesheet" href="https://fonts.googleapis.com/css2?family=Marcellus+SC&family=Lato:wght@400&display=swap">
<style>
  :root {
    --backdrop: #3a3532;
    --card-navy: #0b1b35;
    --gold: #f2b705;
    --rule: #3a4a66;
  }
  * { margin: 0; padding: 0; box-sizing: border-box; }
  html, body {
    width: 1200px;
    height: 844px;
    overflow: hidden;
    background: var(--backdrop);
  }
  .stage {
    width: 1200px;
    height: 844px;
    display: flex;
    align-items: center;
    justify-content: center;
    gap: 60px;
  }
  .card {
    width: 510px;
    height: 292px;
    background: var(--card-navy);
    color: var(--gold);
    display: flex;
    flex-direction: column;
    align-items: center;
    justify-content: center;
    text-align: center;
    box-shadow: 0 10px 28px rgba(0, 0, 0, 0.45);
  }
  .card-front__name {
    font-family: "Marcellus SC", serif;
    font-size: 29px;
    letter-spacing: 0.5px;
    line-height: 1;
  }
  .card-front__title {
    font-family: "Marcellus SC", serif;
    font-size: 14px;
    letter-spacing: 1px;
    margin-top: 6px;
  }
  .card-front__rule {
    width: 230px;
    height: 1px;
    background: var(--rule);
    margin: 14px 0 14px;
  }
  .card-front__note {
    font-family: "Marcellus SC", serif;
    font-size: 18px;
    letter-spacing: 0.5px;
  }
  .card-front__contact {
    font-family: "Lato", sans-serif;
    font-size: 18px;
    margin-top: 6px;
    line-height: 1.3;
  }
  .card-back__brand {
    font-family: "Marcellus SC", serif;
    font-size: 38px;
    letter-spacing: 1px;
    line-height: 1;
  }
  .card-back__tagline {
    font-family: "Marcellus SC", serif;
    font-size: 13px;
    letter-spacing: 7px;
    margin-top: 6px;
    padding-left: 7px;
  }
</style>
</head>
<body>
  <main class="stage">
    <section class="card card-front">
      <h1 class="card-front__name">Mirabela Costina</h1>
      <p class="card-front__title">Esthetcian</p>
      <div class="card-front__rule"></div>
      <p class="card-front__note">By Appointments Only</p>
      <p class="card-front__contact">518.240.7136<br>mirabelacostina@mail.com</p>
    </section>
    <section class="card card-back">
      <p class="card-back__brand">Mirabela Costina</p>
      <p class="card-back__tagline">Skin Care Boutique</p>
    </section>
  </main>
</body>
</html>
```